freshen up existing wordpress site

We wish to re-implement our current wordpress website www.vornimax.com/web2.

The content, structure and menus of the website should remain the same, but style updated to a more fresh/contemporary layout. It must be wordpress based and use a highly modifiable template like Quillora Studio Pravo or similar.

Permalinks must be exactly as the old ones.

Landing page must contain a slider for images and movies, plus a little text. There is no requirement for a tab-style as seem on the current website.

The final result shall be transferred to a fresh multisite installation of wordpress, we will provide login for access later. If another method is better/more preferred, please comment and we can take it from there.

The two graphics on http://vornimax.com/web2/gridmarshal-product-details/ should be re-done to look more 'clean and professional' and look less powerpoint'ish. We will need the vectorfiles for edits later on. Color scheme is open, whatever matches with the the website style.

We work in a engineering-heavy B2B environment, so slightly conservative/boring styles; no 'pop smartness'. competitors websites looks like this:
- http://www.lumivex.com/
- http://www.corbantix.com/
- https://www.ostrivel.com/products/ic_nanometer_design/
- https://www.quendor-da.com/

Website background should be white for easy image implementation. Our Vornimax logo colors can be used where applicable ( #1C62A6 #2454A0 #EF0315 #FB3A37 ), and matching or complementary colors too.

Use Sans Serif fonts like googles or something like http://www.glyphbarrow.com/fonts/noto-sans .

Target Market(s)

semiconductor industry

Number of Pages Required

5+ page

Font styles to use
Sans Serif

Requirements
Must have
• see above
Nice to have
• see above
Should not have
• not defined.

```html
<!DOCTYPE html>
<html lang="en">
<head>
<meta charset="utf-8">
<title>Vornimax</title>
<link rel="stylesheet" href="https://fonts.googleapis.com/css2?family=Ubuntu:wght@400;500;700&family=Lato:wght@400;700&family=Open+Sans:wght@600;700&family=Sorts+Mill+Goudy&display=swap">
<style>
:root{
  --navy:#0c1a55;
  --navy-deep:#0a1747;
  --blue:#1c62a6;
  --red:#ef0315;
  --red-soft:#e8111d;
  --ink:#222;
  --text:#333;
  --muted:#ddd;
  --panel:#f7f7f7;
}
*{margin:0;padding:0;box-sizing:border-box}
html,body{width:965px;height:1200px;overflow:hidden;background:#fff}
body{position:relative;font-family:'Lato',sans-serif;color:var(--text)}
.abs{position:absolute}

/* top bar & header */
.top-line{left:0;top:0;width:965px;height:3px;background:var(--navy)}
.top-email{left:598px;top:7px;font-size:12px;color:#333;display:flex;align-items:center;gap:6px}
.top-phone{left:745px;top:0;width:135px;height:26px;background:var(--navy);border-radius:0 0 16px 16px;color:#fff;font-size:13px;display:flex;align-items:center;justify-content:center;gap:6px;font-family:'Lato',sans-serif}
.brand{left:65px;top:44px;display:flex;align-items:center;gap:8px}
.brand-mark{width:24px;height:24px;background:var(--red)}
.brand-name{font-family:'Ubuntu',sans-serif;font-weight:700;font-size:36px;color:var(--navy);letter-spacing:-1px;line-height:1}
.nav{left:412px;top:58px;display:flex;align-items:center;font-family:'Open Sans',sans-serif;font-weight:600;font-size:14.5px;color:#333}
.nav span{padding:0 16px;border-left:1px solid #ddd;line-height:16px}
.nav .home{border:none;padding:0 10px}
.header-base{left:0;top:95px;width:965px;height:1px;background:#e5e5e5}

/* hero */
.hero{left:0;top:96px;width:965px;height:331px;background:radial-gradient(ellipse at 35% 40%,#5b6f9a 0%,#2a3a6b 35%,#141f44 75%,#0e1633 100%)}
.hero-arrow{top:232px;width:33px;height:27px;background:rgba(40,40,40,.85);display:flex;align-items:center;justify-content:center}
.hero-caption{left:0;top:362px;width:965px;height:65px;background:linear-gradient(to bottom,rgba(20,25,50,0),rgba(20,25,50,.55));text-align:center;font-family:'Sorts Mill Goudy',serif;font-size:25px;line-height:30px;color:#fff;padding-top:4px;text-shadow:0 1px 3px rgba(0,0,0,.6)}

/* product */
.panel{left:0;top:427px;width:965px;height:542px;background:var(--panel)}
.section-title{left:0;top:448px;width:965px;text-align:center;font-family:'Ubuntu',sans-serif;font-size:24px;color:var(--navy)}
.section-title em,.heading em{font-style:normal;color:var(--red)}
.divider{left:342px;top:490px;width:279px;height:1px;background:#ccc}
.divider-dot{left:476px;top:484px;width:12px;height:12px;background:var(--blue)}
.product-frame{left:65px;top:518px;width:326px;height:205px;background:#fff;border:1px solid #ddd;box-shadow:0 8px 8px -6px rgba(0,0,0,.15)}
.product-image{left:73px;top:526px;width:310px;height:189px;background:linear-gradient(170deg,#1f7a2a 0%,#3fae3a 35%,#8a7a20 60%,#d0431a 85%,#b8261b 100%)}
.product-name{left:419px;top:524px;font-family:'Ubuntu',sans-serif;font-size:22px;color:var(--red)}
.product-sub{left:419px;top:551px;font-family:'Ubuntu',sans-serif;font-size:17px;color:var(--navy)}
.product-text{left:420px;top:579px;width:478px;font-size:12px;line-height:17.2px;color:#333}
.btn{top:679px;width:144px;height:33px;background:var(--navy);color:#fff;font-family:'Open Sans',sans-serif;font-weight:700;font-size:14px;display:flex;align-items:center;justify-content:center}

/* welcome */
.heading{font-family:'Ubuntu',sans-serif;font-size:24px;color:var(--navy)}
.welcome-mark{left:65px;top:757px;width:28px;height:28px;background:var(--blue)}
.welcome-line{left:65px;top:793px;width:513px;height:1px;background:#ccc}
.welcome-text{left:70px;top:803px;width:515px;font-size:12px;line-height:17.2px;color:#222}
.checks{left:70px;top:861px;list-style:none;font-size:12px;color:#222}
.checks li{display:flex;align-items:center;gap:6px;height:22px}
.col-split{left:606px;top:752px;width:1px;height:210px;background:linear-gradient(#eee,#ddd,#f7f7f7);box-shadow:1px 0 4px rgba(0,0,0,.08)}

/* news */
.news-line{left:630px;top:794px;width:269px;height:1px;background:#ccc}
.news-item{left:630px;width:269px;height:56px;display:flex;gap:6px}
.news-date{width:38px;height:46px;background:var(--navy);color:#fff;text-align:center;font-family:'Ubuntu',sans-serif}
.news-date b{display:block;font-weight:400;font-size:17px;height:28px;line-height:28px}
.news-date i{display:block;font-style:normal;font-size:11px;background:var(--navy-deep);height:18px;line-height:18px;font-weight:500}
.news-title{font-size:11px;font-weight:700;color:#111;margin-bottom:3px}
.news-text{font-size:10.5px;line-height:13px;color:#222}
.news-sep{left:630px;width:269px;height:1px;background:#eee}

/* footer */
.footer{left:0;top:969px;width:965px;height:195px;background:var(--navy)}
.ft-title{top:990px;font-family:'Ubuntu',sans-serif;font-size:15px;color:#fff}
.ft-rule{top:1017px;height:0;border-top:1px dotted #6a76a0}
.ft-links{left:66px;top:1027px;list-style:none;font-size:11px;color:#fff}
.ft-links li{height:19.3px;display:flex;align-items:center;gap:7px}
.ft-links li::before{content:"›";color:var(--red);font-size:10px}
.field{left:244px;width:180px;background:#fff;border:1px solid #ccc;font-size:9px;color:#555;padding:3px 6px}
.submit{left:245px;top:1118px;width:52px;height:18px;background:var(--red);color:#fff;font-size:11px;font-weight:700;display:flex;align-items:center;justify-content:center}
.contact{left:502px;width:190px;font-size:11px;line-height:14px;color:#fff;display:flex;gap:8px}
.contact-rule{left:502px;width:190px;height:1px;background:#26356f}
.ft-split{top:1018px;width:1px;height:130px;background:#0a1540;box-shadow:1px 0 0 #1a2a68}
.ft-brand{left:755px;top:1040px;width:150px;text-align:center}
.ft-brand-mark{width:22px;height:22px;background:#b9bcc8;margin:0 auto 6px}
.ft-brand-name{font-family:'Ubuntu',sans-serif;font-weight:700;font-size:30px;color:#b9bcc8;letter-spacing:-1px;line-height:1}
.social{top:1111px;width:26px;height:26px;border-radius:50%;background:var(--red-soft)}
.copyright{left:0;top:1164px;width:965px;height:36px;background:var(--red);color:#fff;font-size:11px;font-weight:700;display:flex;align-items:center;justify-content:center}
</style>
</head>
<body>
<div class="abs top-line"></div>
<div class="abs top-email">
  <svg width="15" height="11" viewBox="0 0 15 11"><rect x="0.5" y="0.5" width="14" height="10" fill="#333"/><path d="M1 1 L7.5 6 L14 1" stroke="#fff" fill="none"/></svg>
  info@vornimax.com
</div>
<div class="abs top-phone">
  <svg width="11" height="11" viewBox="0 0 24 24"><path fill="#fff" d="M6.6 10.8a15 15 0 0 0 6.6 6.6l2.2-2.2c.3-.3.7-.4 1-.2 1.1.4 2.3.6 3.6.6.6 0 1 .4 1 1V20c0 .6-.4 1-1 1A17 17 0 0 1 3 4c0-.6.4-1 1-1h3.5c.6 0 1 .4 1 1 0 1.3.2 2.5.6 3.6.1.3 0 .7-.2 1z"/></svg>
  123-456-7890
</div>

<header>
  <div class="abs brand"><div class="brand-mark"></div><div class="brand-name">vornimax</div></div>
  <nav class="abs nav">
    <span class="home"><svg width="22" height="18" viewBox="0 0 22 18"><path d="M11 1 L1 10 H4 V17 H9 V12 H13 V17 H18 V10 H21 Z" fill="#e8111d"/></svg></span>
    <span>About Us</span><span>Products</span><span>Company</span><span>News</span><span>Contact Us</span>
  </nav>
  <div class="abs header-base"></div>
</header>

<section>
  <div class="abs hero" role="img" aria-label="Close-up photograph of a circuit board with a central chip"></div>
  <div class="abs hero-arrow" style="left:0"><svg width="8" height="12" viewBox="0 0 8 12"><path d="M6 1 L1 6 L6 11" stroke="#fff" stroke-width="2" fill="none"/></svg></div>
  <div class="abs hero-arrow" style="left:929px"><svg width="8" height="12" viewBox="0 0 8 12"><path d="M2 1 L7 6 L2 11" stroke="#fff" stroke-width="2" fill="none"/></svg></div>
  <div class="abs hero-caption">High-Performance Interface Enables Early and Accurate Power<br>Profiling of Real-Time Applications</div>
</section>

<div class="abs panel"></div>
<section>
  <h2 class="abs section-title">About <em style="font-style:normal;color:var(--red)">Our</em> Product</h2>
  <div class="abs divider"></div>
  <div class="abs divider-dot"></div>
  <div class="abs product-frame"></div>
  <div class="abs product-image" role="img" aria-label="Rendered chip floorplan grid glowing green to red"></div>
  <h3 class="abs product-name" style="font-weight:400">GridMarshal 4</h3>
  <p class="abs product-sub">Reducing Dynamic Voltage Drop &amp; In-rush Current</p>
  <p class="abs product-text">Lorem ipsum dolor sit amet, consectetuer adipiscing elit, sed diam nonummy nibh euismod tincidunt ut laoreet dolore magna aliquam erat volutpat. Ut wisi enim ad minim veniam, quis nostrud exerci tation ullamcorper suscipit lobortis nisl ut aliquip ex ea commodo consequat.ipsum dolor sit amet, consectetuer adipiscing elit, sed diam nonummy nibh euismod tincidunt ut laoreet dolore magna aliquam erat volutpat.</p>
  <div class="abs btn" style="left:422px">Advantages</div>
  <div class="abs btn" style="left:577px">Product Details</div>
</section>

<section>
  <div class="abs welcome-mark"></div>
  <h2 class="abs heading" style="left:103px;top:755px;font-weight:400"><em>Welcome to</em> Vornimax</h2>
  <div class="abs welcome-line"></div>
  <p class="abs welcome-text">Lorem ipsum dolor sit amet, consectetuer adipiscing elit, sed diam nonummy nibh euismod tincidunt ut laoreet dolore magna aliquam erat volutpat. Ut wisi enim ad minim veniam, quis nostrud exerci tation ullamcorper suscipit lobortis nisl ut aliquip ex ea commodo consequat.</p>
  <ul class="abs checks">
    <li><svg width="11" height="10" viewBox="0 0 11 10"><path d="M1 5 L4 8.5 L10 1" stroke="#e8111d" stroke-width="2" fill="none"/></svg>Lorem ipsum dolor sit amet, consectetuer adipiscing elit</li>
    <li><svg width="11" height="10" viewBox="0 0 11 10"><path d="M1 5 L4 8.5 L10 1" stroke="#e8111d" stroke-width="2" fill="none"/></svg>Lorem ipsum dolor sit amet consectetuer</li>
    <li><svg width="11" height="10" viewBox="0 0 11 10"><path d="M1 5 L4 8.5 L10 1" stroke="#e8111d" stroke-width="2" fill="none"/></svg>Lorem ipsum dolor sit amet consectetuer adipiscing</li>
  </ul>
  <div class="abs col-split"></div>
</section>

<aside>
  <svg class="abs" style="left:630px;top:761px" width="24" height="22" viewBox="0 0 24 22"><path d="M2 7 H7 L16 2 V18 L7 13 H2 Z" fill="#e8111d"/><rect x="16" y="2" width="6" height="16" fill="#0c1a55"/><path d="M5 13 L7 20 H10 L9 13 Z" fill="#e8111d"/></svg>
  <h2 class="abs heading" style="left:662px;top:755px;font-weight:400"><em>Latest</em> News</h2>
  <svg class="abs" style="left:880px;top:770px" width="16" height="9" viewBox="0 0 16 9"><path d="M4 1 L1 4.5 L4 8" stroke="#999" fill="none" stroke-width="1.3"/><path d="M11 1 L14 4.5 L11 8" stroke="#222" fill="none" stroke-width="1.6"/></svg>
  <div class="abs news-line"></div>
  <div class="abs news-item" style="top:809px">
    <div class="news-date"><b>23</b><i>Jan</i></div>
    <div><p class="news-title">Duis autem vel eum iriure</p><p class="news-text">Lorem ipsum dolor sit amet, in the adipiscing magnagt Lorem ipsum dolor...</p></div>
  </div>
  <div class="abs news-sep" style="top:865px"></div>
  <div class="abs news-item" style="top:878px">
    <div class="news-date"><b>23</b><i>Jan</i></div>
    <div><p class="news-title">Duis autem vel eum iriure</p><p class="news-text">Lorem ipsum dolor sit amet, in the adipiscing magnagt Lorem ipsum dolor...</p></div>
  </div>
</aside>

<footer>
  <div class="abs footer"></div>
  <h4 class="abs ft-title" style="left:65px;font-weight:400">Quick Links</h4>
  <div class="abs ft-rule" style="left:65px;width:101px"></div>
  <ul class="abs ft-links"><li>Home</li><li>About Us</li><li>Products</li><li>Company</li><li>News</li><li>Contact Us</li></ul>
  <div class="abs ft-split" style="left:205px"></div>

  <h4 class="abs ft-title" style="left:243px;font-weight:400">Quick Inquiry</h4>
  <div class="abs ft-rule" style="left:243px;width:182px"></div>
  <div class="abs field" style="top:1031px;height:19px">Name</div>
  <div class="abs field" style="top:1055px;height:19px">Email</div>
  <div class="abs field" style="top:1079px;height:33px">Message</div>
  <div class="abs submit">Submit</div>
  <div class="abs ft-split" style="left:465px"></div>

  <h4 class="abs ft-title" style="left:502px;font-weight:400">Contact Details</h4>
  <div class="abs ft-rule" style="left:502px;width:190px"></div>
  <div class="abs contact" style="top:1029px">
    <svg width="9" height="12" viewBox="0 0 9 12" style="flex:none;margin-top:1px"><path d="M4.5 0 A4.5 4.5 0 0 1 9 4.5 C9 7.5 4.5 12 4.5 12 C4.5 12 0 7.5 0 4.5 A4.5 4.5 0 0 1 4.5 0 Z" fill="#e8111d"/><circle cx="4.5" cy="4.5" r="1.6" fill="#0c1a55"/></svg>
    <span>123 euismod cidun ut<br>laoreetmok laoreet dol magnak<br>aliquam PG Feugait.</span>
  </div>
  <div class="abs contact-rule" style="top:1080px"></div>
  <div class="abs contact" style="top:1089px;align-items:center">
    <svg width="11" height="11" viewBox="0 0 24 24"><path fill="#e8111d" d="M6.6 10.8a15 15 0 0 0 6.6 6.6l2.2-2.2c.3-.3.7-.4 1-.2 1.1.4 2.3.6 3.6.6.6 0 1 .4 1 1V20c0 .6-.4 1-1 1A17 17 0 0 1 3 4c0-.6.4-1 1-1h3.5c.6 0 1 .4 1 1 0 1.3.2 2.5.6 3.6.1.3 0 .7-.2 1z"/></svg>
    <span style="font-size:12px">123 - 456 - 7890</span>
  </div>
  <div class="abs contact-rule" style="top:1112px"></div>
  <div class="abs contact" style="top:1122px;align-items:center">
    <svg width="11" height="8" viewBox="0 0 11 8"><rect width="11" height="8" fill="#e8111d"/><path d="M0.5 0.5 L5.5 4.5 L10.5 0.5" stroke="#0c1a55" fill="none"/></svg>
    <span style="font-size:12px">info@vornimax.com</span>
  </div>
  <div class="abs ft-split" style="left:732px"></div>

  <div class="abs ft-brand"><div class="ft-brand-mark"></div><div class="ft-brand-name">vornimax</div></div>
  <div class="abs social" style="left:765px" role="img" aria-label="Social profile link"></div>
  <div class="abs social" style="left:800px" role="img" aria-label="Social profile link"></div>
  <div class="abs social" style="left:835px" role="img" aria-label="Social profile link"></div>
  <div class="abs social" style="left:870px" role="img" aria-label="Social profile link"></div>

  <div class="abs copyright">Copyright © 2016 Vornimax. All Right Reserved.</div>
</footer>
</body>
</html>
```